Wedding Invitation to be used digitally

Design of a Wedding Invitation.
It will be used digitally by whatsapp, so the file format and image size should be appropriate. We don´t intend to print.
Word file with the text contents as attachment. This is REALLY just the text and the main sequencial order of the information that should appear in the invitation.
However, ALL criativity is welcome ofcourse in terms of organization of the information in the paper, font, uppercase and lowercase, numbers and their format, dates and their format, drawings, logo, etc etc

Target Market(s)

family and friends

Requirements
Must have
• A logo at the top with the capitals of our name - R and T
Nice to have
• Should be elegant

```html
<!DOCTYPE html>
<html lang="en">
<head>
<meta charset="UTF-8">
<title>Wedding Invitation – Renata &amp; Tiago</title>
<link href="https://fonts.googleapis.com/css2?family=Playfair+Display:wght@400&display=swap" rel="stylesheet">
<style>
  :root {
    --backdrop: #efebec;
    --paper: #ffffff;
    --frame: #c4ad9a;
    --gold: #a3845f;
    --ink: #1a1a1a;
  }
  * { margin: 0; padding: 0; box-sizing: border-box; }
  html, body { width: 1200px; height: 854px; overflow: hidden; background: var(--backdrop); }
  body { position: relative; font-family: "Playfair Display", Georgia, serif; color: var(--ink); }

  .invitation {
    position: absolute; left: 361px; top: 100px; width: 454px; height: 643px;
    background: var(--paper);
  }
  .invitation__frame {
    position: absolute; left: 32px; top: 39px; width: 390px; height: 565px;
    border: 1.5px solid var(--frame);
  }
  .line {
    position: absolute; left: 0; width: 100%; text-align: center;
    white-space: nowrap; transform: translateY(-50%);
  }
  .monogram { font-size: 78px; line-height: 1; color: var(--gold); letter-spacing: 2px; }
  .kicker { font-size: 10.5px; letter-spacing: 2.4px; }
  .couple-name { font-size: 33px; line-height: 1; color: var(--gold); letter-spacing: 0.5px; }
  .conjunction { font-size: 14px; letter-spacing: 2px; }
  .detail { font-size: 10.3px; line-height: 13px; }
  .rsvp { font-size: 10.5px; letter-spacing: 2.6px; }
</style>
</head>
<body>
  <main class="invitation">
    <div class="invitation__frame"></div>

    <div class="line monogram" style="top:126px">R&amp;T</div>

    <p class="line kicker" style="top:217px">TOGETHER WITH THEIR FAMILIES</p>
    <h1 class="line couple-name" style="top:258px; font-weight:400">RENATA LIMA</h1>
    <p class="line conjunction" style="top:294px">AND</p>
    <h1 class="line couple-name" style="top:328px; font-weight:400">TIAGO SOUSA</h1>

    <p class="line kicker" style="top:376px">INVITE YOU TO THEIR WEDDING CELEBRATION</p>

    <p class="line detail" style="top:412px">SUNDAY, JULY 28, 2024<br>AT 11h30</p>

    <p class="line detail" style="top:451px">CAPELA DE S. JORGE | VILA SERENA<br>(PARKING – MARINA DA COSTA OR PARQUE COSTA AZUL)</p>

    <p class="line detail" style="top:482px">RECEPTION TO FOLLOW</p>

    <p class="line detail" style="top:521px">AT<br>HOTEL FORTE DA AREIA | VILA SERENA<br>(PARKING – ON SITE)</p>

    <p class="line rsvp" style="top:586px">RSVP BY 20TH JULY</p>
  </main>
</body>
</html>
```